business card deign

Logo needs the following on it.
1. attached logo
2. Tagline - "If it chills the cooler or lifts the crowd...we bring it!"
3. Name- Dalton Pikes, Founder and CPO
4. Address - 412 E. Carver Avenue, Ste 2207, Tampa, FL. 33917
5. Phone - 555.318.4726

```html
<!DOCTYPE html>
<html lang="en">
<head>
<meta charset="utf-8">
<title>Kipley Business Card</title>
<link href="https://fonts.googleapis.com/css2?family=Montserrat:wght@400;600;700&display=swap" rel="stylesheet">
<style>
  :root {
    --backdrop: #9a9a9a;
    --card-light: #ffffff;
    --card-dark: #2a2a2a;
    --ink: #2b2b2b;
    --ink-soft: #3a3a3a;
    --ghost: #ececec;
    --paper: #ffffff;
  }
  * { margin: 0; padding: 0; box-sizing: border-box; }
  html, body { width: 1200px; height: 1059px; overflow: hidden; }
  body {
    background: var(--backdrop);
    font-family: "Montserrat", sans-serif;
    position: relative;
  }
  .card {
    position: absolute;
    border-radius: 20px;
    overflow: hidden;
  }
  .card-front {
    left: 256px; top: 89px; width: 688px; height: 390px;
    background: var(--card-light);
    color: var(--ink);
  }
  .card-back {
    left: 253px; top: 569px; width: 694px; height: 389px;
    background: var(--card-dark);
    color: var(--paper);
  }
  .brand-mark {
    position: absolute;
    border-radius: 50%;
  }
  .card-front .brand-mark {
    left: 66px; top: 48px; width: 92px; height: 92px;
    background: var(--ink);
  }
  .brand-name {
    position: absolute;
    font-weight: 700;
    text-transform: uppercase;
    white-space: nowrap;
  }
  .card-front .brand-name {
    left: 35px; top: 158px;
    font-size: 27px; letter-spacing: 13px;
    color: var(--ink);
  }
  .ghost-mark {
    position: absolute;
    left: 400px; top: 150px; width: 210px; height: 210px;
    border-radius: 50%;
    background: var(--ghost);
  }
  .person {
    position: absolute;
    right: 36px; top: 50px;
    text-align: right;
  }
  .person-name {
    font-size: 24px; font-weight: 700; letter-spacing: 0.5px;
    line-height: 1.1; text-transform: uppercase;
  }
  .person-title {
    font-size: 15px; font-weight: 400; margin-top: 4px;
    color: var(--ink-soft);
  }
  .contact {
    position: absolute;
    left: 35px; top: 255px;
    font-size: 15.5px; line-height: 22px;
    color: var(--ink-soft);
  }
  .contact-address { margin-bottom: 9px; }
  .contact-line { display: flex; align-items: center; gap: 7px; height: 25px; }
  .contact-line svg { width: 12px; height: 12px; fill: var(--ink); flex: none; }
  .card-back .brand-mark {
    left: 280px; top: 88px; width: 140px; height: 140px;
    background: var(--paper);
  }
  .card-back .brand-name {
    left: 0; right: 0; top: 246px; text-align: center;
    font-size: 42px; letter-spacing: 20px; padding-left: 20px;
  }
  .tagline {
    position: absolute;
    left: 0; right: 0; top: 340px;
    text-align: center;
    font-size: 15.5px; font-weight: 400;
  }
</style>
</head>
<body>
  <section class="card card-front">
    <div class="brand-mark" aria-hidden="true"></div>
    <div class="brand-name">Kipley</div>
    <div class="ghost-mark" aria-hidden="true"></div>
    <div class="person">
      <div class="person-name">Dalton Pikes</div>
      <div class="person-title">Founder and CPO</div>
    </div>
    <div class="contact">
      <div class="contact-address">412 E. Carver Avenue<br>Ste 2207, Tampa, FL. 33917</div>
      <div class="contact-line">
        <svg viewBox="0 0 12 12" aria-hidden="true"><path d="M1 4c0-2 2-3 5-3s5 1 5 3v1H8.5V3.8h-5V5H1zM2.5 6h7l1 5h-9z"/></svg>
        <span>555.318.4726</span>
      </div>
      <div class="contact-line">
        <svg viewBox="0 0 12 12" aria-hidden="true"><path d="M6 0l6 4v8H0V4zM1.5 5v5.5h9V5L6 8z"/></svg>
        <span>daltonpikes@kipleymail.com</span>
      </div>
    </div>
  </section>

  <section class="card card-back">
    <div class="brand-mark" aria-hidden="true"></div>
    <div class="brand-name">Kipley</div>
    <p class="tagline">If it chills the cooler or lifts the crowd...we bring it!</p>
  </section>
</body>
</html>
```